Front page on www.brightmarkgoods.com modern service ads - each ad for each featured service

We need to have initial 5 banners to be created for our soon to be launched new site,. These are 5 rotating banners that will showcase our companies key features. We are looking for a modern stylish yet simple look to highlight these features. Something thats very inviting and modern to fit the look of the new website.

5 banners need to be, information can be found on www.brightmarkgoods.com about these. Please ask if any questions

Why us?
Art Services
Order Process
Current promotions
Clearance products

please also note. the design will be going onto this website. http://new.brightmarkgoods.com/ Please base actual designs , color schemes etc.. for the new site.

Target Market(s)

Small businesses that purchase marketing promotional goods, to promote their business

Industry/Entity Type

Promotional Product

Font styles to use
Sans Serif

Requirements
Must have
• Size of the banner is 965 x 400 px
Nice to have
• Modern elements,, very clean and minimal look
Should not have
• no cheap generic clip art

```html
<!DOCTYPE html>
<html lang="en">
<head>
<meta charset="utf-8">
<title>Art Services Banner</title>
<link rel="stylesheet" href="https://fonts.googleapis.com/css2?family=Montserrat:wght@700;800&display=swap">
<style>
  :root {
    --page-bg: #f3f3f5;
    --lavender-light: #a4a8d2;
    --lavender-mid: #9095c7;
    --lavender-deep: #7b81b7;
    --headline: #ececf0;
    --tag-box: #b9b9de;
    --tag-text: #f1f1f4;
  }
  * { margin: 0; padding: 0; box-sizing: border-box; }
  html, body {
    width: 1200px; height: 800px; overflow: hidden;
    background: var(--page-bg);
    font-family: "Montserrat", Arial, sans-serif;
  }
  .banner {
    position: absolute; left: 50px; top: 172px;
    width: 1100px; height: 456px; overflow: hidden;
  }
  .banner-backdrop {
    position: absolute; inset: 0;
    background: linear-gradient(160deg, var(--lavender-light) 0%, var(--lavender-mid) 50%, var(--lavender-deep) 100%);
  }
  .headline {
    position: absolute; left: 0; right: 0; top: 80px;
    text-align: center; color: var(--headline);
    font-weight: 800; font-size: 116px; letter-spacing: -3px; line-height: 1;
  }
  .headline .letter-ring {
    display: inline-block; width: 84px; height: 84px;
    border: 19px solid var(--headline); border-radius: 50%;
    margin: 0 2px; vertical-align: -1px;
  }
  .service-list {
    position: absolute; left: 0; right: 0; top: 224px;
    display: flex; flex-direction: column; align-items: center;
    color: var(--tag-text); font-weight: 700; font-size: 38px; line-height: 1;
    letter-spacing: -0.5px;
  }
  .service-list li {
    list-style: none; height: 54px; padding: 0 18px;
    display: flex; align-items: center;
  }
  .service-list li + li { margin-top: -3px; }
  .service-list .boxed { background: var(--tag-box); }
</style>
</head>
<body>
  <section class="banner" aria-label="Artwork services banner">
    <div class="banner-backdrop" role="img" aria-label="Lavender and navy background with diagonal bands and small geometric shapes"></div>
    <h1 class="headline">ARTW<span class="letter-ring" role="img" aria-label="O"></span>RK</h1>
    <ul class="service-list">
      <li class="boxed">FULL ART SERVICES,</li>
      <li>FREE DIGITAL PROOFS,</li>
      <li class="boxed">UNLIMITED PROOF REVISIONS</li>
    </ul>
  </section>
</body>
</html>
```